Awesome Digital Ad Design – Vexora Adloop

I am going to be setting up a Vexora Adloop ad campaign I need creatives for.

Several sizes are needed in the end, however, please submit your design concept in the following 2 sizes to start:
Medium rectangle: 300X250
Leaderboard: 728X90

Original artwork/design files and images used expected upon payment and as part of the final delivery.

Ads should match our company brand and the information on this webpage: http://www.harbelstandwork.com/real-estate-marketing/
SEE MORE INSTRUCTIONS IN ATTACHED WORD DOC

Target Market(s)

Business-To-Business Audience –Real Estate Company Executives (Presidents/VPs/Owners/CEOs/Sales Managers).

Industry/Entity Type

Real Estate

Font styles to use
Sans Serif

Requirements
Must have
• Copy should be minimal words, billboard like. Please use real photos/images that would appeal to real estate high-level decision-maker executives.
Should not have
• No cartoons or graphics

```html
<!DOCTYPE html>
<html lang="en">
<head>
<meta charset="utf-8">
<title>Harbelstand Works – Leaderboard Ad</title>
<link rel="stylesheet" href="https://fonts.googleapis.com/css2?family=Roboto+Condensed:wght@700&family=Roboto:wght@400;500&display=swap">
<style>
  :root {
    --frame: #5b2330;
    --panel: #ffffff;
    --slate: #4e6377;
    --slate-dark: #3b4d5e;
    --band-dark: #33414f;
    --gold: #dcc48f;
    --white: #ffffff;
    --brand-ink: #2f3a44;
    --brand-dot: #8c3344;
    --cta: #f26a1f;
    --cta-dark: #d9560f;
    --rule: rgba(255,255,255,0.45);
  }
  html, body {
    margin: 0;
    padding: 0;
    width: 1200px;
    height: 148px;
    overflow: hidden;
    background: #ffffff;
  }
  .ad {
    position: relative;
    width: 1200px;
    height: 148px;
    box-sizing: border-box;
    border: 3px solid var(--frame);
    background: linear-gradient(90deg, var(--slate-dark) 0%, var(--slate) 40%, var(--slate) 100%);
    overflow: hidden;
    font-family: "Roboto", Arial, sans-serif;
  }
  .brand-panel {
    position: absolute;
    left: 0; top: 0;
    width: 167px;
    height: 100%;
    background: var(--panel);
    display: flex;
    align-items: center;
    justify-content: center;
    gap: 8px;
  }
  .brand-dot {
    width: 12px; height: 12px;
    border-radius: 50%;
    background: var(--brand-dot);
    flex: none;
  }
  .brand-name {
    font-family: "Roboto", Arial, sans-serif;
    font-weight: 500;
    font-size: 17px;
    line-height: 1.15;
    color: var(--brand-ink);
  }
  .headline-band {
    position: absolute;
    left: 178px; top: 12px;
    width: 470px; height: 50px;
    background: linear-gradient(90deg, var(--band-dark) 0%, rgba(51,65,79,0.85) 75%, rgba(51,65,79,0) 100%);
    display: flex;
    align-items: center;
    padding-left: 20px;
    box-sizing: border-box;
  }
  .headline {
    margin: 0;
    font-family: "Roboto Condensed", "Arial Narrow", sans-serif;
    font-weight: 700;
    font-size: 27px;
    letter-spacing: 0.3px;
    color: var(--white);
    text-transform: uppercase;
    white-space: nowrap;
  }
  .headline .accent { color: var(--gold); }
  .divider {
    position: absolute;
    left: 230px; top: 72px;
    width: 360px; height: 1px;
    background: var(--rule);
  }
  .subline {
    position: absolute;
    left: 190px; top: 78px;
    width: 400px;
    margin: 0;
    text-align: center;
    font-size: 22px;
    line-height: 29px;
    color: var(--white);
    text-transform: uppercase;
  }
  .photo {
    position: absolute;
    left: 600px; top: 0;
    width: 395px; height: 100%;
    background:
      linear-gradient(90deg, var(--slate) 0%, rgba(78,99,119,0) 22%, rgba(78,99,119,0) 85%, var(--slate) 100%),
      linear-gradient(180deg, #c9cfd3 0%, #a8b3b8 35%, #6f8a5a 70%, #4f6e3c 100%);
  }
  .cta {
    position: absolute;
    left: 998px; top: 48px;
    width: 174px; height: 46px;
    border-radius: 4px;
    background: linear-gradient(180deg, var(--cta) 0%, var(--cta-dark) 100%);
    color: var(--white);
    font-family: "Roboto", Arial, sans-serif;
    font-weight: 500;
    font-size: 20px;
    text-transform: uppercase;
    text-decoration: none;
    display: flex;
    align-items: center;
    justify-content: center;
    box-shadow: 0 2px 3px rgba(0,0,0,0.3);
  }
</style>
</head>
<body>
  <a class="ad" href="http://www.harbelstandwork.com/real-estate-marketing/" style="display:block;text-decoration:none">
    <div class="brand-panel">
      <span class="brand-dot"></span>
      <span class="brand-name">Harbelstand<br>Works</span>
    </div>
    <div class="photo" role="img" aria-label="Photo of a smiling real estate agent holding a sold sign in front of a house with a green lawn"></div>
    <div class="headline-band">
      <h1 class="headline">Client Follow-Up <span class="accent">Made Simple</span></h1>
    </div>
    <div class="divider"></div>
    <p class="subline">Virtually no cost to<br>your company!</p>
    <span class="cta">Learn More</span>
  </a>
</body>
</html>
```